Business Card Design

I already have a company logo for my company. I have a logo for the manufacturer we represent. I want a professional business card design.

```html
<!DOCTYPE html>
<html lang="en">
<head>
<meta charset="UTF-8">
<title>Signalcrest LLC — Business Card</title>
<link rel="stylesheet" href="https://fonts.googleapis.com/css2?family=Open+Sans:wght@400;600;700&display=swap">
<style>
  :root {
    --stage: #222223;
    --card: #1f1f23;
    --card-edge: #2a2a2f;
    --red: #e31e26;
    --gold: #d4a22a;
    --white: #f4f4f4;
    --pattern-dark: #1b1b1e;
    --pattern-light: #2c2c31;
  }
  * { box-sizing: border-box; margin: 0; padding: 0; }
  html, body {
    width: 1200px; height: 780px; overflow: hidden;
    background: var(--stage);
    font-family: "Open Sans", Arial, sans-serif;
  }
  .stage {
    position: relative; width: 1200px; height: 780px;
  }
  .card {
    position: absolute; top: 235px;
    width: 540px; height: 310px;
    background: var(--card);
    border: 1px solid var(--card-edge);
    overflow: hidden;
    box-shadow: 0 14px 30px rgba(0,0,0,.45);
  }
  .card--front { left: 45px; }
  .card--back { left: 615px; }

  /* Front */
  .brand {
    position: absolute; left: 40px; top: 80px; width: 200px;
    display: flex; align-items: center; gap: 10px;
    color: var(--white); font-weight: 700; font-size: 22px; line-height: 1.1;
    letter-spacing: .5px;
  }
  .brand__mark { width: 18px; height: 18px; background: var(--red); flex: none; }
  .divider {
    position: absolute; left: 0; top: 0; width: 540px; height: 270px;
  }
  .person {
    position: absolute; left: 300px; top: 60px;
  }
  .person__name {
    font-weight: 700; font-size: 30px; line-height: 1.1; color: var(--red);
  }
  .person__name .surname { color: var(--gold); }
  .person__title {
    font-size: 14px; color: var(--white); margin-top: 2px;
  }
  .contacts {
    list-style: none; position: absolute; left: 300px; top: 150px;
  }
  .contacts li {
    display: flex; align-items: center; gap: 9px;
    color: var(--white); font-size: 14px; line-height: 24px;
  }
  .contacts svg { width: 13px; height: 13px; flex: none; }
  .address-band {
    position: absolute; left: 0; bottom: 0; width: 100%; height: 40px;
    background: var(--red);
    color: var(--white); font-size: 14px; font-weight: 600;
    display: flex; align-items: center; padding-left: 40px;
  }

  /* Back */
  .pattern-field {
    position: absolute; inset: 0;
    background: linear-gradient(120deg, var(--pattern-dark) 0%, var(--pattern-light) 60%, var(--pattern-dark) 100%);
  }
  .brand--back {
    left: 0; top: 0; width: 100%; height: 100%;
    justify-content: center; font-size: 32px; gap: 14px;
  }
  .brand--back .brand__mark { width: 24px; height: 24px; }
</style>
</head>
<body>
<main class="stage">

  <section class="card card--front" aria-label="Business card front">
    <div class="brand">
      <span class="brand__mark"></span>
      <span class="brand__name">SIGNALCREST<br>LLC</span>
    </div>

    <svg class="divider" viewBox="0 0 540 270" aria-hidden="true">
      <line x1="285" y1="40" x2="215" y2="250" stroke="var(--gold)" stroke-width="1"/>
    </svg>

    <div class="person">
      <p class="person__name">Tomas <span class="surname">Vlcek</span></p>
      <p class="person__title">Managing Director</p>
    </div>

    <ul class="contacts">
      <li>
        <svg viewBox="0 0 16 16" aria-hidden="true"><path fill="var(--red)" d="M3.6 1.2l2.4 2.6-1.3 1.8c.9 2 2.6 3.7 4.6 4.6l1.8-1.3 2.6 2.4-1.6 2.6C6.6 13.6 2.4 9.4 1 3z"/></svg>
        (555) 014-2287
      </li>
      <li>
        <svg viewBox="0 0 16 16" aria-hidden="true"><rect x="1" y="3" width="14" height="10" rx="1" fill="var(--red)"/><path d="M1.5 3.8L8 9l6.5-5.2" fill="none" stroke="var(--card)" stroke-width="1.3"/></svg>
        info@signalcrest.com
      </li>
      <li>
        <svg viewBox="0 0 16 16" aria-hidden="true"><circle cx="8" cy="8" r="7" fill="var(--red)"/><path d="M1 8h14M8 1c-3 3.5-3 10.5 0 14M8 1c3 3.5 3 10.5 0 14" fill="none" stroke="var(--card)" stroke-width="1"/></svg>
        www.signalcrest.com
      </li>
    </ul>

    <div class="address-band">4410 Lantern Way Suite 120 Cedar Falls, TX 75010</div>
  </section>

  <section class="card card--back" aria-label="Business card back">
    <div class="pattern-field" role="img" aria-label="Faint repeating brand pattern across the card"></div>
    <div class="brand brand--back">
      <span class="brand__mark"></span>
      <span class="brand__name">SIGNALCREST LLC</span>
    </div>
  </section>

</main>
</body>
</html>
```